Brevik Auction Flyer

August 24th thru 27th Online only farm and construction equipment auction Held at brevik auction service Now accepting consignments
Contact Marcus at 810-555-0173 Or Email Marcus@brevikauction-example.com
Accepting consignment now thru August 20th

Industry/Entity Type

Auction Business

```html
<!DOCTYPE html>
<html lang="en">
<head>
<meta charset="utf-8">
<title>Brevik Auction Flyer</title>
<link rel="stylesheet" href="https://fonts.googleapis.com/css2?family=Anton&family=Oswald:wght@500;600&family=Montserrat:wght@500;600;700&display=swap">
<style>
:root{
  --orange:#f7931e;
  --black:#121212;
  --white:#ffffff;
  --paper:#f6f6f4;
  --stage:#a3a4a7;
  --ink:#1a1a1a;
}
*{margin:0;padding:0;box-sizing:border-box}
html,body{width:1200px;height:3655px;overflow:hidden;background:var(--stage)}
.flyer{position:absolute;left:100px;top:1122px;width:1000px;height:1411px;background:var(--paper);overflow:hidden;font-family:"Montserrat",sans-serif}
.hero-photo{position:absolute;left:0;top:0;width:1000px;height:509px;background:linear-gradient(180deg,#5e8fce 0%,#a9c3e0 30%,#c8ccd0 45%,#9a9a96 70%,#7f7d78 100%)}
.band-top{position:absolute;left:0;top:509px;width:1000px;height:57px;background:var(--black)}
.brand-seal{position:absolute;left:102px;top:342px;width:268px;height:268px;border-radius:50%;background:var(--white);border:8px solid var(--orange);display:flex;align-items:center;justify-content:center;text-align:center}
.brand-seal span{font-family:"Oswald",sans-serif;font-weight:600;font-size:34px;line-height:1.05;color:var(--orange);text-transform:uppercase}
.date-panel{position:absolute;left:46px;top:566px;width:383px;height:481px;background:var(--orange);color:var(--white)}
.date-num{position:absolute;font-family:"Anton",sans-serif;font-size:150px;line-height:1}
.date-sup{position:absolute;font-family:"Oswald",sans-serif;font-weight:600;font-size:22px;line-height:1}
.date-month{position:absolute;font-family:"Oswald",sans-serif;font-weight:500;font-size:40px;line-height:1}
.thru{position:absolute;left:54px;top:212px;width:275px;display:flex;align-items:center;gap:12px;font-family:"Montserrat",sans-serif;font-weight:700;font-size:24px;line-height:1;color:var(--ink)}
.thru::before,.thru::after{content:"";flex:1;height:2px;background:var(--ink)}
.online-only{position:absolute;left:60px;top:402px;font-family:"Oswald",sans-serif;font-weight:500;font-size:56px;line-height:1;white-space:nowrap}
.headline{position:absolute;left:467px;top:600px;font-family:"Oswald",sans-serif;font-weight:600;font-size:82px;line-height:88px;color:var(--ink);text-transform:uppercase;letter-spacing:-1px;white-space:nowrap}
.headline small{display:block;font-family:"Montserrat",sans-serif;font-weight:600;font-size:35px;line-height:1.2;color:var(--orange);letter-spacing:1.5px;margin-top:12px}
.venue-pill{position:absolute;left:467px;top:868px;width:491px;height:42px;background:var(--orange);border-radius:6px;display:flex;align-items:center;gap:14px;padding-left:14px;font-weight:700;font-size:20px;color:var(--ink);text-transform:uppercase;white-space:nowrap}
.band-bottom{position:absolute;left:0;top:1047px;width:1000px;height:287px;background:var(--black)}
.consign-title{position:absolute;left:46px;top:1078px;font-family:"Oswald",sans-serif;font-weight:500;font-size:40px;color:var(--orange);text-transform:uppercase}
.deadline-badge{position:absolute;left:711px;top:925px;width:244px;height:244px;border-radius:50%;background:var(--black);border:5px solid var(--orange);color:var(--white);text-align:center;padding-top:40px}
.deadline-badge p{font-size:16px;line-height:1.25;font-weight:500;text-transform:uppercase}
.deadline-badge .thru-small{color:var(--orange);font-weight:700;font-size:14px}
.deadline-badge .deadline-date{font-family:"Oswald",sans-serif;font-size:34px;font-weight:500;color:var(--orange);line-height:1.1;white-space:nowrap}
.deadline-badge sup{font-size:16px}
.features{position:absolute;left:0;top:1158px;width:720px;display:flex}
.feature{width:190px;text-align:center;color:var(--white);border-right:2px dashed #444}
.feature:last-child{border-right:none}
.feature svg{display:block;margin:0 auto 14px}
.feature h3{font-size:14px;font-weight:700;text-transform:uppercase;line-height:1.25}
.feature p{font-size:11.5px;line-height:1.3;margin-top:4px;color:#ddd}
.cart-photo{position:absolute;left:709px;top:1176px;width:280px;height:228px;border-radius:30px 30px 20px 20px;background:linear-gradient(160deg,#6b6e73 0%,#3a3c40 55%,#8a6a52 100%)}
.footer{position:absolute;left:0;top:1334px;width:1000px;height:77px;background:var(--white);display:flex;align-items:center;padding-left:40px}
.contact{display:flex;align-items:center;gap:18px;font-weight:600;font-size:21px;color:var(--ink);margin-right:46px}
.contact-icon{width:38px;height:38px;border-radius:50%;background:var(--orange);display:flex;align-items:center;justify-content:center}
</style>
</head>
<body>
<main class="flyer">
  <div class="hero-photo" role="img" aria-label="Photo of golf carts, a dumper, skid steer and mini excavators lined up in front of storage containers on a gravel lot"></div>
  <div class="band-top"></div>

  <section class="date-panel">
    <span class="date-num" style="left:60px;top:51px">24</span>
    <span class="date-sup" style="left:219px;top:59px">TH</span>
    <span class="date-month" style="left:219px;top:84px">AUGUST</span>
    <div class="thru">THRU</div>
    <span class="date-num" style="left:60px;top:250px">27</span>
    <span class="date-sup" style="left:219px;top:254px">TH</span>
    <span class="date-month" style="left:219px;top:279px">AUGUST</span>
    <span class="online-only">ONLINE ONLY</span>
  </section>

  <div class="brand-seal"><span>Brevik<br>Auction</span></div>

  <h1 class="headline">Farm and<br>Construction<small>EQUIPMENT AUCTION</small></h1>
  <div class="venue-pill">
    <svg width="18" height="24" viewBox="0 0 18 24"><path d="M9 0C4 0 0 4 0 9c0 6.5 9 15 9 15s9-8.5 9-15c0-5-4-9-9-9zm0 12.5A3.5 3.5 0 1 1 9 5.5a3.5 3.5 0 0 1 0 7z" fill="#1a1a1a"/></svg>
    Held at Brevik Auction Service
  </div>

  <section class="band-bottom"></section>
  <h2 class="consign-title">Now Accepting Consignments!</h2>

  <div class="deadline-badge">
    <svg width="40" height="38" viewBox="0 0 40 38"><rect x="2" y="6" width="36" height="30" rx="3" fill="#f7931e"/><rect x="9" y="0" width="4" height="10" fill="#f7931e"/><rect x="27" y="0" width="4" height="10" fill="#f7931e"/><g fill="#121212"><rect x="8" y="16" width="6" height="5"/><rect x="17" y="16" width="6" height="5"/><rect x="26" y="16" width="6" height="5"/><rect x="8" y="25" width="6" height="5"/><rect x="17" y="25" width="6" height="5"/><rect x="26" y="25" width="6" height="5"/></g></svg>
    <p style="margin-top:12px">Accepting<br>consignment now</p>
    <p class="thru-small">THRU</p>
    <p class="deadline-date">AUGUST 20<sup>TH</sup></p>
  </div>

  <div class="features">
    <div class="feature">
      <svg width="56" height="56" viewBox="0 0 56 56"><circle cx="28" cy="28" r="28" fill="#f7931e"/><g fill="none" stroke="#fff" stroke-width="2.5"><circle cx="28" cy="28" r="14"/><ellipse cx="28" cy="28" rx="6" ry="14"/><line x1="14" y1="28" x2="42" y2="28"/><line x1="16" y1="21" x2="40" y2="21"/><line x1="16" y1="35" x2="40" y2="35"/></g></svg>
      <h3>Online Only</h3>
      <p>Bid from anywhere,<br>anytime!</p>
    </div>
    <div class="feature">
      <svg width="56" height="56" viewBox="0 0 56 56"><circle cx="28" cy="28" r="28" fill="#f7931e"/><g fill="none" stroke="#fff" stroke-width="2.5"><rect x="20" y="16" width="12" height="12"/><path d="M14 34V28h26v6"/><circle cx="20" cy="37" r="6"/><circle cx="38" cy="38" r="4"/></g></svg>
      <h3>Farm &amp;<br>Construction</h3>
      <p>Tractors, Excavators,<br>Skid Steers, Attachments,<br>Trailers &amp; More!</p>
    </div>
    <div class="feature">
      <svg width="56" height="56" viewBox="0 0 56 56"><circle cx="28" cy="28" r="28" fill="#f7931e"/><g fill="#fff"><rect x="20" y="14" width="18" height="8" rx="1" transform="rotate(-40 29 18)"/><rect x="27" y="22" width="4" height="16" transform="rotate(-40 29 30)"/><rect x="15" y="38" width="22" height="4"/></g></svg>
      <h3>Easy to Bid</h3>
      <p>Simple online<br>bidding platform.</p>
    </div>
    <div class="feature">
      <svg width="56" height="56" viewBox="0 0 56 56"><circle cx="28" cy="28" r="28" fill="#f7931e"/><text x="28" y="38" text-anchor="middle" font-family="Montserrat, sans-serif" font-weight="700" font-size="28" fill="#fff">$</text></svg>
      <h3>Great Exposure</h3>
      <p>Get top value for<br>your equipment!</p>
    </div>
  </div>

  <div class="cart-photo" role="img" aria-label="Photo of a dark grey six-seat golf cart with brown seats"></div>

  <footer class="footer">
    <div class="contact">
      <span class="contact-icon"><svg width="20" height="20" viewBox="0 0 24 24"><path d="M6.6 10.8a15 15 0 0 0 6.6 6.6l2.2-2.2c.3-.3.7-.4 1-.2 1.1.4 2.3.6 3.6.6.6 0 1 .4 1 1V20c0 .6-.4 1-1 1A17 17 0 0 1 3 4c0-.6.4-1 1-1h3.5c.6 0 1 .4 1 1 0 1.3.2 2.5.6 3.6.1.3 0 .7-.2 1z" fill="#fff"/></svg></span>
      810-555-0173
    </div>
    <div class="contact">
      <span class="contact-icon"><svg width="20" height="16" viewBox="0 0 20 16"><rect x="1" y="1" width="18" height="14" rx="2" fill="none" stroke="#fff" stroke-width="2"/><path d="M1 2l9 7 9-7" fill="none" stroke="#fff" stroke-width="2"/></svg></span>
      Marcus@brevikauction-example.com
    </div>
  </footer>
</main>
</body>
</html>
```